Slider images for online fax service homepage

QuilNet® needs 4 slider images for our newly designed homepage. The slider images should convey professionalism and simplicity without feeling cold or stuffy. The 4th slide is the only one that will contain a video and should be designed with that in mind. Attached to this contest, you will find two .pdf files. One contains a mockup of the new homepage containing dimensions and font requirements. The other is a spreadsheet containing copy for each slide.
In case you are unfamiliar with the brand, QuilNet® is the industry leader in online fax services. We provide faxing capabilities from mobile phones, tablets, and computers with state-of-the-art functionality, such as the ability to sign documents with your finger and send a document to any fax number directly from email.
Updates

FYI:  The dimensions of the video are 640x360.

Hello designers,

We don't want you to think we've forgotten about this contest.  We've been delayed in user testing but hope to have a response soon.

Thank you.

Target Market(s)

Mobile professionals and small businesses who need 24/7 access to fax services, such as lawyers, realtors, truckers, etc.

Industry/Entity Type

Industry

Requirements
Must have
• • The final deliverable should consist of a layered .psd file.
• Dimensions : 1500x475 (viewable area is 1200x475)
• Font is Google font – Lato
• Headline 62pt
• Subhead 32 pt

```html
<!DOCTYPE html>
<html lang="en">
<head>
<meta charset="utf-8">
<title>QuilNet® Homepage Slider Banners</title>
<link href="https://fonts.googleapis.com/css2?family=Lato:wght@400;700;900&display=swap" rel="stylesheet">
<style>
  :root {
    --page-bg: #ececec;
    --panel-blue: #3aa3d2;
    --panel-blue-light: #5fc0e6;
    --headline-bar: rgba(64, 152, 196, 0.9);
    --navy-text: #0f2438;
    --headline-white: #f3f5f7;
    --white: #ffffff;
    --photo-dark: #0b1420;
    --photo-suit: #151f2c;
    --photo-mid: #22405a;
    --photo-server: #35688a;
    --photo-server-glow: rgba(70, 190, 210, 0.35);
    --photo-skin: rgba(190, 150, 135, 0.42);
    --photo-shirt: rgba(140, 190, 225, 0.35);
    --button-blue: #168ad3;
    --button-blue-light: #44b8f0;
  }
  * { margin: 0; padding: 0; box-sizing: border-box; }
  html, body {
    width: 1200px; height: 867px; overflow: hidden;
    background: var(--page-bg);
    font-family: "Lato", Arial, sans-serif;
  }
  .canvas { position: relative; width: 1200px; height: 867px; }

  .banner {
    position: absolute; left: 33px; width: 1135px; height: 360px;
    overflow: hidden;
    box-shadow: 0 2px 6px rgba(0,0,0,0.25);
  }
  .banner--bar { top: 55px; }
  .banner--diagonal { top: 462px; }

  .banner__photo {
    position: absolute; left: 0; top: 0; width: 907px; height: 360px;
    background:
      radial-gradient(ellipse 200px 110px at 62% 78%, var(--photo-skin), transparent 70%),
      radial-gradient(ellipse 90px 60px at 64% 12%, var(--photo-shirt), transparent 75%),
      radial-gradient(ellipse 260px 40px at 40% 52%, rgba(60, 80, 110, 0.5), transparent 75%),
      radial-gradient(ellipse 220px 200px at 14% 45%, var(--photo-server-glow), transparent 75%),
      linear-gradient(90deg, var(--photo-server) 0%, var(--photo-mid) 30%, var(--photo-suit) 52%, var(--photo-dark) 100%);
  }

  .banner__panel {
    position: absolute; right: 0; top: 0; width: 228px; height: 360px;
    background: linear-gradient(180deg, var(--panel-blue-light) 0%, var(--panel-blue) 100%);
    text-align: center;
  }
  .panel__copy {
    margin-top: 22px;
    color: var(--navy-text);
    font-weight: 900;
    font-size: 22.5px;
    line-height: 29px;
    letter-spacing: -0.5px;
    text-transform: uppercase;
  }
  .panel__button {
    position: absolute; left: 27px; top: 266px;
    width: 168px; height: 62px;
    border-radius: 9px;
    background: linear-gradient(180deg, var(--button-blue-light) 0%, var(--button-blue) 100%);
    box-shadow: 0 3px 5px rgba(0,0,0,0.3);
    display: flex; align-items: center;
    color: var(--white); font-weight: 900; font-size: 15.5px;
    letter-spacing: -0.2px;
    text-transform: uppercase;
    white-space: nowrap;
  }
  .panel__button svg { margin: 0 6px 0 10px; flex: none; }

  .headline-bar {
    position: absolute; left: 0; top: 296px; width: 832px; height: 52px;
    background: var(--headline-bar);
    color: var(--headline-white);
    font-size: 46px; font-weight: 700; line-height: 52px;
    letter-spacing: -0.3px;
    padding-left: 13px;
    text-shadow: 1px 2px 3px rgba(0,0,0,0.5);
    white-space: nowrap;
  }

  .diagonal-shape { position: absolute; left: 0; top: 0; }
  .headline-stack {
    position: absolute; left: 22px; top: 24px;
    color: var(--headline-white);
    font-size: 46.5px; font-weight: 700; line-height: 56.5px;
    letter-spacing: -0.3px;
    text-shadow: 1px 2px 3px rgba(0,0,0,0.5);
    white-space: nowrap;
  }
  .brand {
    position: absolute; left: 22px; top: 226px;
    display: flex; align-items: center; gap: 6px;
    color: var(--navy-text); font-size: 29px; font-weight: 900;
    letter-spacing: -0.5px;
  }
  .brand__dot { width: 26px; height: 26px; border-radius: 50%; background: var(--navy-text); }
</style>
</head>
<body>
<div class="canvas">

  <section class="banner banner--bar">
    <div class="banner__photo" role="img" aria-label="Businessman in a dark suit holding a tablet in front of server racks"></div>
    <div class="headline-bar">The Fast, Smart and Secure Way to Fax</div>
    <aside class="banner__panel">
      <p class="panel__copy">Send and<br>receive<br>faxes easily<br>and<br>securely by<br>email.<br>No paper<br>needed.</p>
      <div class="panel__button">
        <svg width="32" height="32" viewBox="0 0 32 32" aria-hidden="true">
          <circle cx="16" cy="16" r="15" fill="#0e5f97" stroke="#7fd0f5" stroke-width="1.5"/>
          <path d="M13 10 L19 16 L13 22" fill="none" stroke="#fff" stroke-width="3" stroke-linecap="round" stroke-linejoin="round"/>
        </svg>
        Start Faxing
      </div>
    </aside>
  </section>

  <section class="banner banner--diagonal">
    <div class="banner__photo" role="img" aria-label="Businessman in a dark suit holding a tablet in front of server racks"></div>
    <svg class="diagonal-shape" width="907" height="360" viewBox="0 0 907 360" aria-hidden="true">
      <defs>
        <linearGradient id="diagonalFill" x1="0" y1="0" x2="0" y2="1">
          <stop offset="0" stop-color="#4ab2dc"/>
          <stop offset="1" stop-color="#3a9fcd"/>
        </linearGradient>
      </defs>
      <polygon points="0,0 712,0 0,358" fill="url(#diagonalFill)"/>
    </svg>
    <h2 class="headline-stack">The Fast,<br>Smart and Secure<br>Way to Fax</h2>
    <div class="brand"><span class="brand__dot"></span>QuilNet®</div>
    <aside class="banner__panel">
      <p class="panel__copy">Send and<br>receive<br>faxes easily<br>and<br>securely by<br>email.<br>No paper<br>needed.</p>
      <div class="panel__button">
        <svg width="32" height="32" viewBox="0 0 32 32" aria-hidden="true">
          <circle cx="16" cy="16" r="15" fill="#0e5f97" stroke="#7fd0f5" stroke-width="1.5"/>
          <path d="M13 10 L19 16 L13 22" fill="none" stroke="#fff" stroke-width="3" stroke-linecap="round" stroke-linejoin="round"/>
        </svg>
        Start Faxing
      </div>
    </aside>
  </section>

</div>
</body>
</html>
```